SaaS Early tech startup business card design

Unique design for experience ecommerce platform company. the business cards will be used by executive members. conformance with color code is required.

```html
<!DOCTYPE html>
<html lang="en">
<head>
<meta charset="utf-8">
<title>Velto Business Card</title>
<link href="https://fonts.googleapis.com/css2?family=Arimo:wght@400;700&display=swap" rel="stylesheet">
<style>
  :root {
    --page-bg: #e9ecef;
    --navy: #22213a;
    --deep-blue: #0b5d8a;
    --blue: #12809f;
    --teal: #1fb89c;
    --teal-light: #4cc7ae;
    --grey-text: #666a70;
    --white: #ffffff;
  }
  * { margin: 0; padding: 0; box-sizing: border-box; }
  html, body {
    width: 1200px; height: 900px; overflow: hidden;
    background: var(--page-bg);
    font-family: "Arimo", Arial, sans-serif;
  }
  .canvas { position: relative; width: 1200px; height: 900px; }

  .card {
    position: absolute;
    width: 700px; height: 400px;
    border-radius: 28px;
    overflow: hidden;
    box-shadow: 0 14px 30px rgba(0,0,0,0.18);
  }

  /* Front */
  .card-front {
    left: 60px; top: 50px;
    background: linear-gradient(100deg, var(--deep-blue) 0%, var(--blue) 45%, var(--teal) 100%);
  }
  .front-brand {
    position: absolute; left: 0; right: 0; top: 50%;
    transform: translateY(-50%);
    text-align: center;
    font-weight: 700; font-size: 120px; letter-spacing: -2px;
    color: var(--white);
  }

  /* Back */
  .card-back {
    left: 440px; top: 450px;
    background: var(--white);
  }
  .back-accent {
    position: absolute; left: 0; top: 150px;
    width: 10px; height: 60px; background: var(--teal);
  }
  .person {
    position: absolute; left: 40px; top: 150px;
  }
  .person-name {
    font-weight: 700; font-size: 30px; color: var(--teal);
  }
  .person-role {
    margin-top: 4px; font-size: 20px; color: var(--grey-text);
  }
  .back-brand {
    position: absolute; right: 50px; top: 40px;
    font-weight: 700; font-size: 92px; letter-spacing: -2px;
    color: var(--blue);
  }
  .divider {
    position: absolute; left: 0; right: 0; top: 252px; height: 8px;
    background: linear-gradient(90deg, var(--deep-blue) 0%, var(--blue) 50%, var(--teal-light) 50%, var(--teal) 100%);
  }
  .contact-band {
    position: absolute; left: 0; right: 0; top: 260px; bottom: 0;
    background: var(--navy);
    display: flex; justify-content: space-between; align-items: center;
    padding: 0 40px;
  }
  .contact-list { list-style: none; }
  .contact-item {
    display: flex; align-items: center; gap: 12px;
    color: var(--white); font-size: 20px; line-height: 1.45;
  }
  .contact-icon {
    width: 24px; height: 24px; border-radius: 5px;
    background: var(--teal);
    display: flex; align-items: center; justify-content: center;
  }
  .address {
    color: var(--white); font-size: 19px; line-height: 1.35; text-align: right;
  }
</style>
</head>
<body>
<div class="canvas">

  <section class="card card-front" aria-label="Card front">
    <div class="front-brand">velto</div>
  </section>

  <section class="card card-back" aria-label="Card back">
    <div class="back-brand">velto</div>
    <div class="back-accent"></div>
    <div class="person">
      <div class="person-name">Daniel Reyes</div>
      <div class="person-role">Manager</div>
    </div>
    <div class="divider"></div>
    <div class="contact-band">
      <ul class="contact-list">
        <li class="contact-item">
          <span class="contact-icon">
            <svg width="14" height="14" viewBox="0 0 24 24"><path fill="#22213a" d="M6.6 10.8a15 15 0 0 0 6.6 6.6l2.2-2.2c.3-.3.7-.4 1-.2 1.1.4 2.3.6 3.6.6.6 0 1 .4 1 1V20c0 .6-.4 1-1 1A17 17 0 0 1 3 4c0-.6.4-1 1-1h3.5c.6 0 1 .4 1 1 0 1.3.2 2.5.6 3.6.1.3 0 .7-.2 1z"/></svg>
          </span>
          555-014-7320
        </li>
        <li class="contact-item">
          <span class="contact-icon">
            <svg width="15" height="12" viewBox="0 0 24 18"><rect x="1" y="1" width="22" height="16" rx="1" fill="none" stroke="#22213a" stroke-width="2"/><path d="M1 1l11 9 11-9" fill="none" stroke="#22213a" stroke-width="2"/></svg>
          </span>
          daniel@veltohq.com
        </li>
        <li class="contact-item">
          <span class="contact-icon">
            <svg width="15" height="15" viewBox="0 0 24 24" fill="none" stroke="#22213a" stroke-width="2"><circle cx="12" cy="12" r="10"/><path d="M2 12h20M12 2c3 3 3 17 0 20M12 2c-3 3-3 17 0 20"/></svg>
          </span>
          www.veltohq.com
        </li>
      </ul>
      <p class="address">42 Marlow Street,<br>Easton OR 97310</p>
    </div>
  </section>

</div>
</body>
</html>
```